Health and Wellbeing online Shop

I have attached a specification, however in summary this is a new business startup selling vitamins and supplements.

We need a web design for new wellbeing website, selling high end vitamins, supplements and nootropics. Therefore I need a simple eCommerce solution .

I need the website to look very different to other websites on the market. The more creative the better. It should look fresh elegant and simple. The criteria for products being on my site is that they have great reviews and they have been scientifically tested.

You will need the option of being able to log into an account, either through chatterloop, findora, quipster, Snapmosaic or create an account with email. For accounts, users will need the facility to reset passwords, see previous orders, track current order, and maintain favourites.

It should be PC, mobile and tablet friendly.

Look and Feel

It should be an elegant, modern, professional, trendy, unisex website. It should look clean and calm. Am happy to try interesting and slightly unusual designs. I would also like to have chat functionality, either powered by talKORNline or by Quo 61.

Websites I like are
https://www.plume-radiance.example.co.uk/
https://www.mereherbals.example.co.uk/
http://www.novadermis.example.com/

PLEASE DO USE YOUR KNOWELDGE OF WHAT WORKS FOR WEB DESIGN. YOU’RE THE EXPERT AND NEED YOUR EXPERTISE. CARTE BLANCHE TO DESIGN AS YOU SEE FIT. Please be creative, I need my site to stand out from the crowd.

Target Market(s)
Middle aged women are our most common client, however, younger patients, both male and female, will often visit the site. In summary, I would like the site to appeal to all age brackets.

Industry/Entity Type
Business

Coding
Coded - Design and coding required

Number of Pages Required
5 pages
Updates

I would like more designs. I was expecting 75+ Designs to choose from as per the package I paid for.

Target Market(s)

Industry/Entity Type

Health And Wellness

Coding

Number of Pages Required

5+ page

Requirements
Must have
• Creative design

```html
<!DOCTYPE html>
<html lang="en">
<head>
<meta charset="utf-8">
<title>Lumeva Skin Clinic – Home</title>
<link href="https://fonts.googleapis.com/css2?family=Open+Sans:wght@400;600;700;800&family=Lato:wght@400;700&display=swap" rel="stylesheet">
<style>
:root{
  --orange:#f26522;
  --ink:#222;
  --text:#444;
  --line:#e3e3e3;
  --soft:#f4f4f4;
  --dark:#2d2d2d;
  --white:#fff;
  --hero-a:#f6c6ac;
  --hero-b:#f9d5c1;
}
*{box-sizing:border-box;margin:0;padding:0}
html,body{width:1200px;height:2651px;overflow:hidden;background:var(--white)}
body{font-family:'Lato',sans-serif;color:var(--text);position:relative}
.abs{position:absolute}
/* top bar */
.topbar{left:0;top:0;width:1200px;height:50px;background:var(--soft);font-family:'Open Sans',sans-serif;font-size:13px;font-weight:600;color:var(--ink)}
.topbar span{position:absolute;top:16px;display:flex;align-items:center;gap:8px}
/* header */
.brand{left:79px;top:74px;height:104px;display:flex;align-items:center;gap:16px}
.brand-dot{width:104px;height:104px;border:2px solid #444;border-radius:50%}
.brand-name{font-family:'Lato',sans-serif;font-size:26px;font-weight:400;color:#333;letter-spacing:3px}
.search{left:501px;top:80px;width:479px;height:43px;border:1px solid #bbb;font-family:'Open Sans',sans-serif;font-size:13px;color:#333;padding:13px 16px}
.search svg{position:absolute;right:16px;top:12px}
.cart{left:996px;top:84px;display:flex;align-items:center;gap:12px;font-family:'Open Sans',sans-serif;font-size:13px;color:#222}
.cart i{width:36px;height:36px;border-radius:50%;background:var(--orange);display:flex;align-items:center;justify-content:center}
.nav{top:151px;right:80px;display:flex;gap:45px;font-family:'Open Sans',sans-serif;font-size:15px;color:#222}
.nav .on{font-weight:700}
/* hero */
.hero{left:0;top:194px;width:1200px;height:568px;background:linear-gradient(90deg,var(--hero-a) 0%,var(--hero-b) 50%,#f7cbb2 100%);overflow:hidden}
.hero-photo{position:absolute;left:580px;top:0;width:620px;height:568px;background:radial-gradient(ellipse at 70% 45%,#eab39a 0%,#f3c6ae 45%,rgba(247,203,178,0) 75%)}
.hero-title{position:absolute;left:93px;top:178px;font-family:'Open Sans',sans-serif;font-weight:800;font-size:56px;line-height:64px;color:#3a3a3a;letter-spacing:.5px}
.hero-sub{position:absolute;left:95px;top:245px;font-family:'Open Sans',sans-serif;font-weight:700;font-size:25px;line-height:31px;color:#3a3a3a}
.btn-orange{background:var(--orange);color:#fff;font-family:'Open Sans',sans-serif;font-weight:700;letter-spacing:1px;display:flex;align-items:center;justify-content:center}
.hero-shop{position:absolute;left:96px;top:340px;width:127px;height:36px;font-size:14px}
.hero-arrow{position:absolute;top:266px}
/* sidebar */
.side-box{left:75px;width:241px;border:2px solid var(--line)}
.side-head{height:64px;border-bottom:2px solid var(--line);display:flex;align-items:center;justify-content:space-between;padding:0 20px;font-family:'Open Sans',sans-serif;font-weight:800;font-size:22px;color:var(--ink);letter-spacing:.5px}
.side-box.closed .side-head{border-bottom:none;height:62px}
.side-list{list-style:none;padding:11px 0 0 20px}
.side-list li{height:43.4px;display:flex;align-items:center;font-size:15px;color:#333}
.side-list li b{width:34px;font-size:17px;font-weight:700;color:#222}
.side-list li.more{color:#c8161d;font-weight:700}
.side-list li.more b{color:#c8161d}
/* products */
.section-title{font-family:'Open Sans',sans-serif;font-weight:800;font-size:21px;color:var(--ink);letter-spacing:.5px}
.sort{left:857px;top:823px;display:flex;align-items:center;gap:10px;font-family:'Open Sans',sans-serif;font-weight:700;font-size:15px;color:#222}
.sort .sel{width:121px;height:34px;border:1px solid var(--line);font-weight:400;display:flex;align-items:center;justify-content:space-between;padding:0 14px}
.pager{left:1073px;top:830px;display:flex;gap:8px}
.pager i{width:22px;height:22px;border-radius:50%;background:#777;display:flex;align-items:center;justify-content:center}
.card{width:241px;height:387px;border:2px solid #eaeaea;text-align:center}
.card-img{margin:14px auto 0;width:198px;height:190px;border-radius:6px;background:linear-gradient(180deg,#fafafa 0%,#e4e4e4 100%)}
.card h3{margin-top:17px;font-family:'Open Sans',sans-serif;font-weight:700;font-size:15px;color:#222;letter-spacing:.5px}
.card p{margin:8px auto 0;width:205px;font-size:13.5px;line-height:21px;color:#555}
.price{margin-top:4px;font-family:'Open Sans',sans-serif;font-size:17px;color:#222}
.price b{color:var(--orange);font-weight:700}
.btn-dark{background:#111;color:#fff;font-family:'Open Sans',sans-serif;font-weight:700;font-size:13px;letter-spacing:1px;display:inline-flex;align-items:center;justify-content:center}
.card .btn-dark{margin-top:12px;width:139px;height:36px}
/* welcome */
.welcome{left:342px;top:1714px;width:785px;height:351px;background:var(--soft);padding:32px 25px}
.welcome h2{font-family:'Open Sans',sans-serif;font-weight:800;font-size:32px;line-height:40px;color:var(--ink);letter-spacing:.5px}
.welcome h2 span{font-size:39px}
.welcome p{margin-top:14px;width:725px;font-size:15.3px;line-height:26px;color:#444}
.welcome .btn-dark{margin-top:24px;width:139px;height:36px}
.perk{top:2086px;width:246px;height:121px;border:2px solid var(--line);text-align:center;padding-top:22px;font-family:'Open Sans',sans-serif;font-weight:600;font-size:18px;color:#222}
.perk svg{display:block;margin:0 auto 8px;height:38px}
/* footer */
.footer{left:0;top:2261px;width:1200px;height:322px;background:#f2f2f2}
.fcol{top:2301px}
.fcol h4{font-family:'Open Sans',sans-serif;font-weight:800;font-size:19px;color:var(--ink);letter-spacing:.5px;margin-bottom:8px}
.fcol ul{list-style:none;font-size:13.5px;color:#444}
.fcol li{height:30.5px;display:flex;align-items:center}
.contact p{font-size:14px;line-height:23px;color:#444}
.contact .name{font-family:'Open Sans',sans-serif;font-weight:700;font-size:15px;color:#222;margin-bottom:6px}
.contact .row{display:flex;align-items:center;gap:18px;margin-top:6px}
.email{top:2343px;left:884px;width:242px;height:36px;background:#fff;border:1px solid var(--line);font-size:12px;color:#333;padding:11px 12px}
.signup{top:2391px;left:1037px;width:89px;height:40px;font-size:12px}
.social{top:2500px;left:885px;display:flex;gap:17px}
.social i{width:26px;height:26px;border-radius:5px;background:#8a8a8a;display:block}
.bottom{left:0;top:2583px;width:1200px;height:68px;background:var(--dark);color:#fff;font-size:12.5px}
.cards{position:absolute;right:73px;top:23px;display:flex;gap:18px}
.cards i{width:41px;height:26px;background:#fff;border-radius:3px;display:block}
</style>
</head>
<body>

<div class="abs topbar">
  <span style="left:75px"><svg width="16" height="12" viewBox="0 0 16 12"><rect x="0" y="1" width="10" height="8" fill="#222"/><path d="M10 4h3l3 3v2h-6z" fill="#222"/><circle cx="3.5" cy="10" r="1.8" fill="#222"/><circle cx="12.5" cy="10" r="1.8" fill="#222"/></svg>FREE ShippingOn Order Over $149</span>
  <span style="left:352px"><svg width="14" height="14" viewBox="0 0 14 14"><rect width="14" height="14" rx="2" fill="#222"/><path d="M4 3l2 2-1 1.5c.7 1.4 1.6 2.3 3 3l1.5-1 2 2-1.2 1.2C7 11.5 2.5 7 2.8 4.2z" fill="#fff"/></svg>+44 20 7946 0321</span>
  <span style="left:977px">Log In</span>
  <span style="left:1043px">My Account</span>
</div>

<header>
  <div class="abs brand"><div class="brand-dot"></div><div class="brand-name">LUMEVA</div></div>
  <div class="abs search">SEARCH
    <svg width="18" height="18" viewBox="0 0 18 18"><circle cx="7.5" cy="7.5" r="5.5" fill="none" stroke="#222" stroke-width="2.5"/><path d="M11.5 11.5L16 16" stroke="#222" stroke-width="2.8" stroke-linecap="round"/></svg>
  </div>
  <div class="abs cart"><i><svg width="16" height="14" viewBox="0 0 16 14"><path d="M1 1h2.5l2 8h7.5l2-6H4.5" fill="none" stroke="#fff" stroke-width="1.8"/><circle cx="6.5" cy="12" r="1.3" fill="#fff"/><circle cx="12" cy="12" r="1.3" fill="#fff"/></svg></i>MY CART (0)</div>
  <nav class="abs nav"><span class="on">HOME</span><span>VITAMINS</span><span>NOOTROPICS</span><span>CONTACT</span><span>ABOUT US</span></nav>
</header>

<section class="abs hero">
  <div class="hero-photo" role="img" aria-label="Woman with hair in a bun holding a white supplement bottle on her fingertips"></div>
  <h1 class="hero-title">LUMEVA SKIN</h1>
  <p class="hero-sub">Excepteur sint occaecat cupidatat<br>non proident voluptatem.</p>
  <div class="btn-orange hero-shop">SHOP NOW</div>
  <svg class="hero-arrow" style="left:36px" width="24" height="40" viewBox="0 0 24 40"><path d="M20 4L5 20l15 16" fill="none" stroke="#fff" stroke-width="5"/></svg>
  <svg class="hero-arrow" style="left:1140px" width="24" height="40" viewBox="0 0 24 40"><path d="M4 4l15 16L4 36" fill="none" stroke="#fff" stroke-width="5"/></svg>
</section>

<aside>
  <div class="abs side-box" style="top:809px;height:607px">
    <div class="side-head">CATEGORIES <svg width="14" height="10" viewBox="0 0 14 10"><path d="M2 2l5 5 5-5" fill="none" stroke="#222" stroke-width="3"/></svg></div>
    <ul class="side-list">
      <li><b>»</b>Amino Acids</li><li><b>»</b>Antioxidants</li><li><b>»</b>Cannabis Oil CBD</li><li><b>»</b>Chondroitin</li><li><b>»</b>Coenzyme Q10</li><li><b>»</b>Cod Liver Oil</li><li><b>»</b>Essential Fatty Acids</li><li><b>»</b>Evening Primrose Oils</li><li><b>»</b>Fish Oils</li><li><b>»</b>Glucosamine</li><li><b>»</b>Herbal / Botanical</li><li class="more"><b>»</b>More</li>
    </ul>
  </div>
  <div class="abs side-box" style="top:1435px;height:607px">
    <div class="side-head">INTEREST <svg width="14" height="10" viewBox="0 0 14 10"><path d="M2 2l5 5 5-5" fill="none" stroke="#222" stroke-width="3"/></svg></div>
    <ul class="side-list">
      <li><b>»</b>Ageing</li><li><b>»</b>Bone Health</li><li><b>»</b>Children &amp;&nbsp; Health</li><li><b>»</b>Circulation</li><li><b>»</b>Digestive Health</li><li><b>»</b>Energy</li><li><b>»</b>Eye Health</li><li><b>»</b>Heart Health</li><li><b>»</b>Immune System</li><li><b>»</b>Joints &amp;amp; Muscles</li><li><b>»</b>Memory</li><li class="more"><b>»</b>More</li>
    </ul>
  </div>
  <div class="abs side-box closed" style="top:2060px;height:66px"><div class="side-head">DELIVERY <svg width="10" height="14" viewBox="0 0 10 14"><path d="M2 2l5 5-5 5" fill="none" stroke="#222" stroke-width="3"/></svg></div></div>
  <div class="abs side-box closed" style="top:2142px;height:66px"><div class="side-head">NEW</div></div>
</aside>

<main>
  <h2 class="abs section-title" style="left:342px;top:826px">FEATURED PRODUCTS</h2>
  <div class="abs sort">Sort by: <div class="sel">Name <svg width="8" height="12" viewBox="0 0 8 12"><path d="M0 5l4-5 4 5zM0 7l4 5 4-5z" fill="#222"/></svg></div></div>
  <div class="abs pager">
    <i><svg width="8" height="10" viewBox="0 0 8 10"><path d="M6 1L2 5l4 4" fill="none" stroke="#fff" stroke-width="2.2"/></svg></i>
    <i><svg width="8" height="10" viewBox="0 0 8 10"><path d="M2 1l4 4-4 4" fill="none" stroke="#fff" stroke-width="2.2"/></svg></i>
  </div>

  <div class="abs card" style="left:345px;top:887px"><div class="card-img" role="img" aria-label="Three white supplement bottles"></div><h3>BODY CARE</h3><p>Vestibulum ante ipsum primis in faucibus orci.</p><div class="price"><b>$35/</b>Per Bottle</div><span class="btn-dark">ADD TO CART</span></div>
  <div class="abs card" style="left:615px;top:887px"><div class="card-img" role="img" aria-label="Three white supplement bottles"></div><h3>BODY CARE</h3><p>Vestibulum ante ipsum primis in faucibus orci.</p><div class="price"><b>$35/</b>Per Bottle</div><span class="btn-dark">ADD TO CART</span></div>
  <div class="abs card" style="left:885px;top:887px"><div class="card-img" role="img" aria-label="Three white supplement bottles"></div><h3>BODY CARE</h3><p>Vestibulum ante ipsum primis in faucibus orci.</p><div class="price"><b>$35/</b>Per Bottle</div><span class="btn-dark">ADD TO CART</span></div>
  <div class="abs card" style="left:345px;top:1294px"><div class="card-img" role="img" aria-label="Three white supplement bottles"></div><h3>BODY CARE</h3><p>Vestibulum ante ipsum primis in faucibus orci.</p><div class="price"><b>$35/</b>Per Bottle</div><span class="btn-dark">ADD TO CART</span></div>
  <div class="abs card" style="left:615px;top:1294px"><div class="card-img" role="img" aria-label="Three white supplement bottles"></div><h3>BODY CARE</h3><p>Vestibulum ante ipsum primis in faucibus orci.</p><div class="price"><b>$35/</b>Per Bottle</div><span class="btn-dark">ADD TO CART</span></div>
  <div class="abs card" style="left:885px;top:1294px"><div class="card-img" role="img" aria-label="Three white supplement bottles"></div><h3>BODY CARE</h3><p>Vestibulum ante ipsum primis in faucibus orci.</p><div class="price"><b>$35/</b>Per Bottle</div><span class="btn-dark">ADD TO CART</span></div>

  <section class="abs welcome">
    <h2>WELCOME TO<br><span>LUMEVA SKIN CLINIC</span></h2>
    <p>Welcome to Lumeva Skin Clinic, leading supplier of skincare and beauty products. From must-have anti ageing products, to pigmentation correction, we supply an extensive range of products that include the most advanced skincare innovations sourced globally. Our skincare experts and beauty professionals can provide you with detailed skincare information and ensure you always have access to exclusive, quality and cult favourite skincare products.</p>
    <span class="btn-dark">READ MORE</span>
  </section>

  <div class="abs perk" style="left:343px"><svg width="42" height="34" viewBox="0 0 42 34"><rect x="0" y="4" width="26" height="20" rx="2" fill="#666"/><path d="M27 10h8l6 7v7H27z" fill="#666"/><circle cx="9" cy="28" r="5" fill="#666" stroke="#fff" stroke-width="2"/><circle cx="33" cy="28" r="5" fill="#666" stroke="#fff" stroke-width="2"/></svg>Free Shipping</div>
  <div class="abs perk" style="left:612px"><svg width="32" height="38" viewBox="0 0 32 38"><path d="M2 2h28v16c0 10-8 16-14 18C10 34 2 28 2 18z" fill="#666"/><path d="M16 8v22c4-2 8-6 8-12V8z" fill="#fff"/></svg>Secure Shopping</div>
  <div class="abs perk" style="left:881px"><svg width="44" height="36" viewBox="0 0 44 36"><path d="M14 2L2 14l12 12v-7c12 0 20 4 26 15 0-14-10-22-26-23z" fill="#666"/><path d="M22 2L10 14l12 12" fill="none" stroke="#666" stroke-width="3"/></svg>Easy Return Policy</div>
</main>

<footer>
  <div class="abs footer"></div>
  <div class="abs fcol" style="left:75px"><h4>QUICK LINKS</h4><ul><li>Home</li><li>Shop All</li><li>Anti-Ageing</li><li>Collagen</li><li>Skin Lightening</li><li>Skin Peels</li><li>Contact us</li></ul></div>
  <div class="abs fcol" style="left:340px"><h4>INFORMATION</h4><ul><li>Shipping Informations</li><li>Return Policy</li><li>About us</li><li>Contact us</li><li>Terms &amp; Conditions</li><li>Privacy Policy</li></ul></div>
  <div class="abs fcol contact" style="left:611px"><h4>CONTACT US</h4>
    <p class="name">Lumeva Skin Clinic</p>
    <p>Orchard Court,<br>42 Linden Row, London,<br>N0 4QZ.</p>
    <p class="row"><svg width="14" height="14" viewBox="0 0 14 14"><path d="M3 1l3 3-1.5 2c1 2 2 3 4 4l2-1.5 3 3-2 2C6 13 1 8 1 3z" fill="#222"/></svg>+44 1632 960418</p>
    <p class="row"><svg width="14" height="11" viewBox="0 0 14 11"><rect width="14" height="11" fill="#222"/><path d="M0 0l7 6 7-6" fill="none" stroke="#fff" stroke-width="1.2"/></svg>hello@lumevaclinic.example.com</p>
  </div>
  <div class="abs fcol" style="left:883px"><h4>NEWSLETTER SIGN UP</h4></div>
  <div class="abs email">Email Address</div>
  <div class="abs btn-orange signup">SIGN UP</div>
  <div class="abs fcol" style="left:883px;top:2460px"><h4>FOLLOW US</h4></div>
  <div class="abs social"><i></i><i></i><i></i><i></i><i></i><i></i></div>
  <div class="abs bottom">
    <span style="position:absolute;left:76px;top:27px">Copyright © 2021.Company Name. All Right Reserved</span>
    <div class="cards"><i></i><i></i><i></i><i></i></div>
  </div>
</footer>

</body>
</html>
```